real esate business card with company logo and name

we need a business card design for a real esate company

The company name is Walsh & Brand Pty Ltd, and we have our logo designed and will upload. We want classic or moden feel. Black or white background. looks more textured. Should include folowinginformations
Owen Walsh and Lucy Brand
Sales Agents & Onsite Manager
p: 07 5948 2063
F: 07 5948 2174
M:0431 857 219
3/42 Marlow Crescent, FERNLEA QLD 4213

We want this business card looks professonal. Thank you in advance.

Industry/Entity Type

Real Estate Agent

Contact Information for Business Card

Owen Walsh and Lucy Brand
Onsite Manager & Sales Agents
p: 07 5948 2063
M:0431 857 219

Font styles to use
Serif

Colors
000000
fbfbfb
333333
959595

Requirements
Must have
• company logo and name, black or white back ground

```html
<!DOCTYPE html>
<html lang="en">
<head>
<meta charset="utf-8">
<title>Walsh &amp; Brand Pty Ltd — Business Card</title>
<link href="https://fonts.googleapis.com/css2?family=Lato:wght@400;700&family=Oswald:wght@400&display=swap" rel="stylesheet">
<style>
  :root {
    --black: #000000;
    --stage: #333333;
    --band-grey: #cfcfd1;
    --back-light: #e9e9eb;
    --mark-grey: #6b6b6d;
    --brand-grey: #959595;
    --ink: #111111;
  }
  * { margin: 0; padding: 0; box-sizing: border-box; }
  html, body { width: 1200px; height: 1086px; overflow: hidden; }
  body { background: var(--stage); position: relative; font-family: "Lato", sans-serif; }

  .card {
    position: absolute;
    left: 254px;
    width: 677px;
    overflow: hidden;
    box-shadow: 0 4px 14px rgba(0,0,0,0.45);
  }
  .card--front { top: 126px; height: 386px; background: var(--black); }
  .card--back { top: 587px; height: 385px; background: var(--back-light); }

  .brand-square {
    position: absolute;
    background: var(--mark-grey);
  }
  .card--front .brand-square { left: 270px; top: 32px; width: 130px; height: 130px; }
  .card--back .brand-square { left: 299px; top: 138px; width: 80px; height: 80px; }

  .brand-name {
    position: absolute;
    left: 0; width: 100%;
    text-align: center;
    font-family: "Oswald", sans-serif;
    font-weight: 400;
    color: var(--brand-grey);
    letter-spacing: 0.5px;
    white-space: nowrap;
  }
  .card--front .brand-name { top: 186px; font-size: 21px; }
  .card--back .brand-name { top: 232px; font-size: 13px; }

  .info-band {
    position: absolute;
    left: 0; top: 243px;
    width: 100%; height: 121px;
    background: var(--band-grey);
  }
  .info-divider {
    position: absolute;
    left: 340px; top: 0;
    width: 3px; height: 100%;
    background: var(--black);
  }
  .agent {
    position: absolute;
    right: 357px; top: 6px;
    text-align: right;
    color: var(--ink);
  }
  .agent-name { font-weight: 700; font-size: 29px; line-height: 36px; }
  .agent-role { font-weight: 400; font-size: 21px; line-height: 24px; }

  .contact {
    position: absolute;
    left: 361px; top: 4px;
    color: var(--ink);
    list-style: none;
  }
  .contact-line {
    display: flex; align-items: center;
    font-size: 19px; line-height: 22.5px;
  }
  .contact-line svg { width: 14px; height: 14px; margin-right: 7px; flex: none; }
  .address { margin-top: 7px; font-size: 16px; line-height: 20px; }

  .back-band {
    position: absolute;
    left: 0; top: 105px;
    width: 100%; height: 181px;
    background: var(--black);
  }
</style>
</head>
<body>

  <section class="card card--front">
    <div class="brand-square"></div>
    <p class="brand-name">WALSH &amp; BRAND PTY LTD.</p>

    <div class="info-band">
      <div class="agent">
        <p class="agent-name">Owen Walsh</p>
        <p class="agent-role">Sales Agents</p>
      </div>
      <div class="info-divider"></div>
      <ul class="contact">
        <li class="contact-line">
          <svg viewBox="0 0 14 14" aria-hidden="true"><rect x="3.5" y="0.8" width="7" height="12.4" rx="1.2" fill="none" stroke="#111" stroke-width="1.4"/><circle cx="7" cy="11" r="0.8" fill="#111"/></svg>
          0431 857 219
        </li>
        <li class="contact-line">
          <svg viewBox="0 0 14 14" aria-hidden="true"><path d="M1 5 Q7 1 13 5 L11.5 6.5 L9.5 5.5 L9.5 4 Q7 3.3 4.5 4 L4.5 5.5 L2.5 6.5 Z" fill="#111"/><path d="M3 8 L5 6 H9 L11 8 V12 H3 Z" fill="#111"/></svg>
          07 5948 2063
        </li>
        <li class="contact-line">
          <svg viewBox="0 0 14 14" aria-hidden="true"><rect x="4" y="1" width="6" height="4" fill="#111"/><rect x="1" y="5" width="12" height="5" rx="1" fill="#111"/><rect x="4" y="9" width="6" height="4" fill="#fff" stroke="#111" stroke-width="1"/></svg>
          07 5948 2174
        </li>
        <li class="address">3/42 Marlow Crescent<br>FERNLEA QLD 4213</li>
      </ul>
    </div>
  </section>

  <section class="card card--back">
    <div class="back-band"></div>
    <div class="brand-square"></div>
    <p class="brand-name">WALSH &amp; BRAND PTY LTD.</p>
  </section>

</body>
</html>
```